Trendy, rustic, patriotic Facebook Design!

Would like something to catch people's eye! Must include our logo and phone number. 318-507-4429. Dogs in the project are a must. Bold pricing, location, etc to catch peoples eyes is a plus.

Target Market(s)

Dog owners

Font styles to use
Serif
Sans Serif

Colors
1f66ae
ec1f27
ffffff

Requirements
Must have
• Dogs, company logo, business phone 318-507-4429 and website www.brindlepawco.com
Nice to have
• Something that is rustic, trendy!
Should not have
• Cartoons.

```html
<!DOCTYPE html>
<html lang="en">
<head>
<meta charset="utf-8">
<title>Brindle Paw Co. — Facebook Cover</title>
<link href="https://fonts.googleapis.com/css2?family=Arvo:wght@400;700&family=Oswald:wght@700&family=Open+Sans:wght@400&display=swap" rel="stylesheet">
<style>
  :root {
    --navy: #062d6b;
    --navy-deep: #0e2a5c;
    --steel: #5a6f92;
    --concrete: #c4c4c4;
    --concrete-light: #d6d6d6;
    --white: #ffffff;
    --fur-light: #b8936a;
    --fur-mid: #8a6a4e;
    --fur-dark: #4a3a32;
    --collar-red: #9e2a24;
  }
  html, body { margin: 0; padding: 0; overflow: hidden; }
  .cover {
    position: relative;
    width: 1200px;
    height: 450px;
    overflow: hidden;
    background:
      linear-gradient(90deg, var(--concrete-light) 0%, var(--concrete) 35%, #a5adb9 55%, var(--steel) 72%, var(--navy-deep) 100%);
  }
  .ribbon { position: absolute; left: 0; top: 0; width: 1200px; height: 450px; }
  .price {
    position: absolute;
    left: 190px; top: 65px; width: 476px; height: 85px;
    margin: 0;
    display: flex; align-items: center; justify-content: center;
    font-family: "Arvo", serif; font-weight: 400;
    font-size: 60px; line-height: 1; color: var(--navy);
    letter-spacing: 0.5px;
  }
  .headline {
    position: absolute;
    left: 112px; top: 152px; width: 660px;
    margin: 0;
    display: flex; align-items: baseline; white-space: nowrap;
    color: var(--navy);
  }
  .headline .slab {
    font-family: "Arvo", serif; font-weight: 400; font-size: 60px; line-height: 1;
  }
  .headline .accent {
    font-family: "Oswald", sans-serif; font-weight: 700; font-style: italic;
    font-size: 100px; line-height: 1; margin: 0 18px 0 16px;
    transform: skewX(-8deg); display: inline-block; letter-spacing: 0;
  }
  .blurb {
    position: absolute;
    left: 165px; top: 310px; width: 540px;
    margin: 0;
    text-align: center; color: var(--white);
    font-family: "Arvo", serif; font-size: 20px; line-height: 27px;
  }
  .blurb .lead {
    font-family: "Oswald", sans-serif; font-weight: 700; font-style: italic;
    font-size: 31px; letter-spacing: -0.5px; margin-right: 6px;
  }
  .contact {
    position: absolute; top: 412px;
    display: flex; align-items: center; gap: 6px;
    font-family: "Open Sans", sans-serif; font-size: 17px; color: var(--navy);
  }
  .contact svg { width: 25px; height: 25px; }
  .contact--phone { left: 219px; }
  .contact--web { left: 414px; letter-spacing: -0.6px; }
  .dog-collage { position: absolute; left: 842px; top: 27px; width: 358px; height: 423px; }
</style>
</head>
<body>
<main class="cover">
  <svg class="ribbon" viewBox="0 0 1200 450" aria-hidden="true">
    <polygon points="129,75 181,75 181,139 129,139 155,107" fill="var(--white)"/>
    <polygon points="675,75 728,75 706,107 728,139 675,139" fill="var(--white)"/>
    <rect x="190" y="65" width="476" height="85" fill="var(--white)"/>
  </svg>
  <h1 class="price">PRICE HERE</h1>
  <h2 class="headline">
    <span class="slab">TEXT</span><span class="accent">HERE</span><span class="slab">&amp; HERE</span>
  </h2>
  <p class="blurb"><span class="lead">SAMPLE</span>lorem ipsum dolor sit amet,<br>consectetuer adipiscing elit, sed diam nonummy</p>

  <div class="contact contact--phone">
    <svg viewBox="0 0 24 24" aria-hidden="true">
      <circle cx="12" cy="12" r="10.5" fill="none" stroke="var(--navy)" stroke-width="2"/>
      <rect x="8.5" y="6" width="7" height="12" rx="1.2" fill="var(--navy)" transform="rotate(30 12 12)"/>
    </svg>
    <span>318-507-4429</span>
  </div>
  <div class="contact contact--web">
    <svg viewBox="0 0 24 24" aria-hidden="true">
      <circle cx="12" cy="12" r="10.5" fill="none" stroke="var(--navy)" stroke-width="2"/>
      <circle cx="12" cy="12" r="7" fill="none" stroke="var(--navy)" stroke-width="1.5"/>
      <ellipse cx="12" cy="12" rx="3" ry="7" fill="none" stroke="var(--navy)" stroke-width="1.3"/>
      <line x1="5" y1="12" x2="19" y2="12" stroke="var(--navy)" stroke-width="1.3"/>
      <line x1="6" y1="8.5" x2="18" y2="8.5" stroke="var(--navy)" stroke-width="1.1"/>
      <line x1="6" y1="15.5" x2="18" y2="15.5" stroke="var(--navy)" stroke-width="1.1"/>
    </svg>
    <span>www.brindlepawco.com</span>
  </div>

  <svg class="dog-collage" viewBox="0 0 358 423" role="img" aria-label="Photo collage of many dogs of different breeds grouped together, with a red collar across the lower part">
    <defs>
      <linearGradient id="collage-tones" x1="0" y1="0" x2="0.3" y2="1">
        <stop offset="0" stop-color="var(--fur-mid)"/>
        <stop offset="0.45" stop-color="var(--fur-light)"/>
        <stop offset="0.8" stop-color="var(--fur-dark)"/>
        <stop offset="1" stop-color="var(--collar-red)"/>
      </linearGradient>
    </defs>
    <rect x="0" y="0" width="358" height="423" fill="url(#collage-tones)" opacity="0.9"/>
  </svg>
</main>
</body>
</html>
```